Holiday Rental Company Flyer Design (DL not A5)

Note from Brandloom Administration: The category sizing selected is A5, however the project requires DL sized artwork. Please refer to the DL template link below while the 'Special Requirements' are updated accordingly.

Project Brief:
We need a double sided DL flyer designed for an up market Holiday Rental Company that portrays a personalised approach to property management. These are to be used for letter box drops to homes we're specifically targeting so the design should be modern, complimentary colour palette, uncluttered & visually appealing.

Please Download the DL Template from Quillora here: http://www.quillora.com.au/ql/ns/propath/UploadResources.aspx?selectedTab=0?pfid=KMT&pf_id=KMT&xnav=easypath-upload-image#Templates

Target Market(s)

Wealthy Home Owners

Industry/Entity Type

It Company

Other font styles liked:
• Avant Garde Extra Light & Demi

Colors
33b8a4

Requirements
Must have
• DL Flyer sizes (210mm width x 99mm width, plus 3mm bleed)
• Front: Logo, Main Image & Grab
• Back: Contact Details & Brief Description of our business
• Images: Ideally the main image should be the house with the pool but alternatively a lifestyle images could also be used.
Nice to have
• A creative designer!
Should not have
• Clutter & busy designs

```html
<!DOCTYPE html>
<html lang="en">
<head>
<meta charset="utf-8">
<title>Tidewater Stays – DL Flyer</title>
<link href="https://fonts.googleapis.com/css2?family=Questrial&family=Raleway:wght@200;300&display=swap" rel="stylesheet">
<style>
  :root{
    --teal:#33b8a4;
    --teal-deep:#23a28f;
    --teal-pale:#92d8cb;
    --white:#ffffff;
    --ink:#4a4a4a;
    --page:#e9eeee;
  }
  *{margin:0;padding:0;box-sizing:border-box;}
  html,body{width:1200px;height:1000px;overflow:hidden;background:var(--page);}
  body{position:relative;font-family:"Questrial",sans-serif;}

  .flyer{position:absolute;left:120px;width:960px;height:453px;overflow:hidden;box-shadow:0 4px 14px rgba(0,0,0,.18);}
  .flyer--front{top:32px;background:var(--teal);}
  .flyer--back{top:515px;background:var(--white);}
  .flyer svg.shapes{position:absolute;inset:0;width:100%;height:100%;}

  /* front */
  .brand-panel{position:absolute;left:630px;top:36px;width:310px;text-align:center;color:var(--white);}
  .brand-name{font-family:"Raleway",sans-serif;font-weight:200;font-size:38px;line-height:42px;letter-spacing:5px;text-transform:uppercase;}
  .brand-dot{width:34px;height:34px;border:1.5px solid var(--white);border-radius:50%;margin:14px auto 18px;}
  .brand-rule{width:260px;height:1px;background:var(--white);margin:0 auto 18px;opacity:.9;}
  .tagline{font-family:"Raleway",sans-serif;font-weight:200;font-size:27px;line-height:31px;letter-spacing:1px;text-transform:uppercase;}
  .grab{display:inline-block;margin-top:6px;background:var(--white);color:var(--teal);font-family:"Raleway",sans-serif;font-weight:300;font-size:14px;letter-spacing:1.5px;padding:6px 18px;text-transform:uppercase;}

  /* back */
  .back-brand{position:absolute;left:40px;top:30px;display:flex;align-items:center;gap:10px;color:var(--white);font-family:"Raleway",sans-serif;font-weight:200;font-size:22px;letter-spacing:3px;text-transform:uppercase;}
  .back-brand .brand-dot{margin:0;width:22px;height:22px;}
  .contact-invite{position:absolute;left:40px;top:112px;width:220px;color:var(--white);font-size:17px;line-height:22px;}
  .contact-phone{position:absolute;left:40px;top:262px;color:var(--white);font-size:17px;}
  .contact-address{position:absolute;left:40px;top:318px;color:var(--white);font-size:17px;line-height:22px;}
  .contact-bar{position:absolute;left:0;right:0;bottom:0;height:48px;display:flex;align-items:center;justify-content:center;gap:40px;color:var(--white);font-size:19px;letter-spacing:.5px;}

  .about{position:absolute;left:452px;top:36px;width:480px;color:var(--ink);font-size:16px;line-height:21px;}
  .about-title{color:var(--teal);font-size:21px;margin-bottom:16px;}
  .about p{margin-bottom:16px;}
  .highlight{color:var(--teal);}
  .about-list{list-style:none;margin-top:4px;}
  .about-list li{height:30px;line-height:30px;}
</style>
</head>
<body>

<section class="flyer flyer--front">
  <svg class="shapes" viewBox="0 0 960 453" aria-hidden="false">
    <defs>
      <linearGradient id="photoTone" x1="0" y1="0" x2="1" y2="1">
        <stop offset="0" stop-color="#d9a45a"/>
        <stop offset="0.35" stop-color="#5a3f7c"/>
        <stop offset="0.6" stop-color="#2c2470"/>
        <stop offset="1" stop-color="#2a6fd0"/>
      </linearGradient>
    </defs>
    <path d="M0 0 H470 C610 70 650 300 540 453 H0 Z" fill="url(#photoTone)" stroke="#ffffff" stroke-width="4" role="img" aria-label="Photograph of a modern luxury home at dusk with a lit swimming pool"/>
  </svg>
  <div class="brand-panel">
    <div class="brand-name">Tidewater<br>Stays</div>
    <div class="brand-dot"></div>
    <div class="brand-rule"></div>
    <div class="tagline">Holiday<br>Rental<br>Management</div>
    <div class="grab">With a difference</div>
  </div>
</section>

<section class="flyer flyer--back">
  <svg class="shapes" viewBox="0 0 960 453">
    <defs>
      <linearGradient id="cushionTone" x1="0" y1="0" x2="1" y2="1">
        <stop offset="0" stop-color="#f1e2b8"/>
        <stop offset="1" stop-color="#c9a93a"/>
      </linearGradient>
      <linearGradient id="seaTone" x1="0" y1="0" x2="0" y2="1">
        <stop offset="0" stop-color="#6fd3e2"/>
        <stop offset="1" stop-color="#2a9fc2"/>
      </linearGradient>
    </defs>
    <path d="M0 0 H330 C300 120 290 260 400 330 C520 400 760 395 960 380 V453 H0 Z" fill="var(--teal)"/>
    <rect x="420" y="283" width="540" height="26" fill="var(--teal-pale)"/>
    <rect x="0" y="405" width="960" height="48" fill="var(--teal-pale)"/>
    <circle cx="360" cy="140" r="64" fill="var(--teal-pale)"/>
    <circle cx="360" cy="140" r="55" fill="url(#cushionTone)" role="img" aria-label="Photograph of cushions on a bed"/>
    <circle cx="372" cy="300" r="64" fill="var(--teal-pale)"/>
    <circle cx="372" cy="300" r="55" fill="url(#seaTone)" role="img" aria-label="Photograph of swimmers in clear blue sea"/>
  </svg>

  <div class="back-brand"><span class="brand-dot"></span>Tidewater Stays</div>
  <p class="contact-invite">If you'd like to know what your property could achieve or require additional information, please contact us on:</p>
  <p class="contact-phone">t: (03) 5900 2417</p>
  <p class="contact-address">PO Box 12,<br>Seacliff Victoria 3999</p>

  <div class="about">
    <h2 class="about-title">What we do differently!</h2>
    <p>Rather than relying upon a key safe or a central pick-up destination, a 'Tidewater Stays' staff member will greet guests upon arrival.</p>
    <p>Our <span class="highlight">'Meet &amp; Greet'</span> service provides home owners with an increased level of Security and also allows us to:</p>
    <ul class="about-list">
      <li>Prepare the home for their arrival (lights, heaters, music etc.)</li>
      <li>Establish a rapport &amp; help facilitate future bookings</li>
      <li>Reiterate their responsibilities to ensure the return of their bond</li>
    </ul>
  </div>

  <div class="contact-bar">
    <span>e: stay@tidewaterstays.com.au</span>
    <span>|</span>
    <span>w: tidewaterstays.com.au</span>
  </div>
</section>

</body>
</html>
```